Tallon Electrical Business Card

We need a business card design for our family-run electrical contracting business based in Western Australia called 'Tallon Electrical'. We provide electrical services including residential, commercial and industrial. We aim for individual business cards to be made for all of our employees. We already have a company logo, which we require to be featured on the design. We would like simple, sleek and vibrant designs, which incorporate our logo and represent our business. We do not want anything involving too many graphics/images. We like the colours red, black, white and all shades of grey. The final design should communicate professionalism and trustworthiness.
We require the following contact information:
Name- Grant Pellow
EC 5871
Mobile number- 0455 870 219
Fax number (including area code)- (08) 9560 2831
Email adress- name@tallonelectrical.com.au
Electrical
- ITC Handel Bold

```html
<!DOCTYPE html>
<html lang="en">
<head>
<meta charset="utf-8">
<title>Tallon Electrical – Business Card</title>
<link rel="stylesheet" href="https://fonts.googleapis.com/css2?family=Arimo:wght@400;700&display=swap">
<style>
  :root {
    --backdrop: #3a3a3a;
    --red: #e3262b;
    --red-deep: #c81e23;
    --card-white: #f7f7f7;
    --ink-dark: #3b3b3b;
    --ink-mid: #6b6b6b;
    --rule: #d6d6d6;
  }
  * { box-sizing: border-box; margin: 0; padding: 0; }
  html, body { width: 1200px; height: 874px; overflow: hidden; }
  body {
    background: var(--backdrop);
    font-family: "Arimo", Arial, sans-serif;
    display: flex;
    align-items: center;
    justify-content: center;
    gap: 50px;
  }
  .card {
    width: 540px;
    height: 327px;
    position: relative;
    box-shadow: 0 10px 30px rgba(0,0,0,.45);
  }

  /* Back of card */
  .card-back {
    background: radial-gradient(ellipse at center, var(--red) 0%, var(--red-deep) 100%);
    color: #fff;
    display: flex;
    flex-direction: column;
    align-items: center;
    justify-content: center;
    gap: 22px;
  }
  .card-back .brand-name {
    font-weight: 700;
    font-size: 34px;
    letter-spacing: 1px;
    text-transform: uppercase;
  }
  .card-back .website {
    font-size: 15px;
    font-weight: 400;
    letter-spacing: .5px;
  }

  /* Front of card */
  .card-front {
    background: linear-gradient(180deg, #ffffff 0%, var(--card-white) 60%, #ececec 100%);
  }
  .brand {
    position: absolute;
    left: 120px;
    top: 62px;
    display: flex;
    align-items: center;
    gap: 10px;
  }
  .brand-mark {
    width: 26px;
    height: 26px;
    background: var(--red);
  }
  .card-front .brand-name {
    font-weight: 700;
    font-size: 24px;
    color: var(--ink-dark);
    text-transform: uppercase;
    letter-spacing: .5px;
  }
  .person {
    position: absolute;
    left: 40px;
    top: 188px;
  }
  .person-name {
    color: var(--red);
    font-weight: 700;
    font-size: 15px;
  }
  .person-role {
    color: var(--ink-mid);
    font-size: 12px;
    margin-top: 3px;
  }
  .divider {
    position: absolute;
    left: 285px;
    top: 128px;
    width: 1px;
    height: 100px;
    background: var(--rule);
  }
  .contact {
    position: absolute;
    left: 305px;
    top: 128px;
    list-style: none;
    font-size: 11px;
    color: var(--ink-mid);
    line-height: 1.35;
  }
  .contact li {
    display: flex;
    gap: 9px;
    margin-bottom: 5px;
  }
  .contact svg {
    flex: none;
    width: 11px;
    height: 11px;
    margin-top: 1px;
    fill: var(--red);
  }
</style>
</head>
<body>

  <section class="card card-back" aria-label="Card back">
    <div class="brand-name">Tallon Electrical</div>
    <div class="website">www.tallonelectrical.com.au</div>
  </section>

  <section class="card card-front" aria-label="Card front">
    <div class="brand">
      <span class="brand-mark"></span>
      <span class="brand-name">Tallon Electrical</span>
    </div>

    <div class="person">
      <div class="person-name">Grant Pellow</div>
      <div class="person-role">Director</div>
    </div>

    <div class="divider"></div>

    <ul class="contact">
      <li>
        <svg viewBox="0 0 12 12" aria-hidden="true"><path d="M6 0a4 4 0 0 0-4 4c0 3 4 8 4 8s4-5 4-8a4 4 0 0 0-4-4zm0 5.5A1.5 1.5 0 1 1 6 2.5a1.5 1.5 0 0 1 0 3z"/></svg>
        <span>EC 5871, address<br>town here 6010</span>
      </li>
      <li>
        <svg viewBox="0 0 12 12" aria-hidden="true"><path d="M3 0h6a1 1 0 0 1 1 1v10a1 1 0 0 1-1 1H3a1 1 0 0 1-1-1V1a1 1 0 0 1 1-1zm.5 1.5v8h5v-8z"/></svg>
        <span>0455 870 219</span>
      </li>
      <li>
        <svg viewBox="0 0 12 12" aria-hidden="true"><path d="M3 0h6v3H3zM1 4h10a1 1 0 0 1 1 1v4H9v3H3V9H0V5a1 1 0 0 1 1-1zm3 5v2h4V9z"/></svg>
        <span>(08) 9560 2831</span>
      </li>
      <li>
        <svg viewBox="0 0 12 12" aria-hidden="true"><path d="M0 2h12v8H0zm1 1v.4l5 3.3 5-3.3V3z"/></svg>
        <span>name@tallonelectrical.com.au</span>
      </li>
    </ul>
  </section>

</body>
</html>
```